Website for BrightlineLabs presentation

We need a new website, ideally as a wordpress there, for BrightlineLabs - we focus on machine learning, big data, data science and data analytics. This website should have two main sections - team presentation, introduction and offered services as static pages, and a blog section.

Target Market(s)

Companies which would like to hire the consultants for data science

Industry/Entity Type

Data Service

Font styles to use
Sans Serif

Colors

Designer to choose colors to be used in the design.

Requirements
Must have
• Wordpress template, blog and presentation pages, nice background images, incorporate the existing logo from brief
Nice to have
• match the word and ppt existing templates for brightline labs

```html
<!DOCTYPE html>
<html lang="en">
<head>
<meta charset="utf-8">
<title>Brightline Labs</title>
<link href="https://fonts.googleapis.com/css2?family=Maven+Pro:wght@400;500;600&family=Montserrat:wght@400;500&display=swap" rel="stylesheet">
<style>
:root{
  --blue:#1a8dc8;
  --blue-deep:#0f6fa3;
  --ink:#1c2a35;
  --text:#6f7780;
  --muted:#9aa1a8;
  --topbar:#121619;
  --line:#e3e6e9;
  --band:#ececec;
  --pale:#f3f6f9;
  --white:#ffffff;
}
*{margin:0;padding:0;box-sizing:border-box}
html,body{width:1200px;height:3529px;overflow:hidden}
body{position:relative;background:var(--white);font-family:"Montserrat",sans-serif;color:var(--text)}
.abs{position:absolute}
h1,h2,h3,.brand{font-family:"Maven Pro",sans-serif;font-weight:500}

/* top bar */
.topbar{left:0;top:0;width:1200px;height:52px;background:var(--topbar);color:#e8e8e8;font-size:14px}
.topbar .item{position:absolute;top:0;height:52px;display:flex;align-items:center;gap:10px}
.topbar svg{fill:#fff}

/* nav */
.nav{left:0;top:52px;width:1200px;height:84px;background:var(--white);box-shadow:0 2px 6px rgba(0,0,0,.08)}
.brand{position:absolute;left:78px;top:26px;display:flex;align-items:center;gap:10px;color:var(--blue);font-size:22px;font-weight:600;letter-spacing:1px}
.brand .dot{width:14px;height:14px;border-radius:50%;background:var(--blue)}
.menu{position:absolute;right:78px;top:0;height:84px;display:flex;align-items:center;gap:44px;font-size:13px;letter-spacing:.5px;color:#b5b9bd}
.menu .active{color:var(--ink)}

/* hero */
.hero{left:0;top:136px;width:1200px;height:572px;background:radial-gradient(circle at 78% 45%,#0d6f93 0%,#0a2f45 30%,#06131d 70%)}
.hero h1{position:absolute;left:78px;top:176px;font-size:44px;color:#fff;font-weight:400;letter-spacing:1px}
.hero p{position:absolute;left:78px;top:246px;width:580px;font-size:16px;line-height:25px;color:#d9e2e8}
.btn{display:flex;align-items:center;justify-content:center;background:var(--blue);color:#fff;font-family:"Maven Pro",sans-serif;font-size:18px;border:1px solid #5ec2ef}
.hero .btn{position:absolute;left:78px;top:339px;width:188px;height:50px}

/* services */
.deco{border-radius:50%}
.services-title{left:0;top:766px;width:1200px;text-align:center;color:var(--blue);font-size:46px;letter-spacing:1px;font-weight:400}
.services-sub{left:320px;top:836px;width:560px;text-align:center;font-size:13px;line-height:22px}
.spine{left:599px;top:1010px;width:2px;height:760px;background:var(--line)}
.node{width:104px;height:104px;border-radius:50%;background:#fff;box-shadow:0 4px 14px rgba(0,0,0,.12);display:flex;align-items:center;justify-content:center}
.node svg{stroke:var(--blue);fill:none;stroke-width:2}
.badge{width:30px;height:30px;border-radius:50%;color:#fff;font-size:16px;display:flex;align-items:center;justify-content:center;font-family:"Maven Pro",sans-serif}
.badge.on{background:var(--blue)}.badge.off{background:#c5c8cb}
.service h3{font-size:30px;color:var(--blue);font-weight:400;margin-bottom:18px}
.service p{font-size:13.5px;line-height:23px;margin-bottom:20px}
.service a{font-size:14px;color:var(--blue);text-decoration:underline;letter-spacing:.5px}
.service.left{text-align:right;width:376px}
.service.right{text-align:left;width:376px}

/* about */
.band{left:0;top:2224px;width:1200px;height:611px;background:var(--band)}
.about{left:78px;top:1986px;width:1044px;height:390px;border-radius:8px;background:linear-gradient(180deg,#0c1418,#1c2a2f 50%,#0b1013);overflow:hidden}
.about h2{position:absolute;top:60px;width:100%;text-align:center;color:var(--blue);font-size:44px;font-weight:400}
.about p{position:absolute;left:90px;width:864px;text-align:center;color:#e6e6e6;font-size:13px;line-height:23px}
.about .btn{position:absolute;left:428px;top:278px;width:188px;height:50px}

/* blogs */
.blogs-title{left:0;top:2434px;width:1200px;text-align:center;color:var(--blue);font-size:46px;font-weight:400}
.card{top:2513px;width:313px}
.card .photo{height:153px}
.card p{margin-top:16px;font-size:14px;line-height:22px;color:var(--muted);padding-bottom:12px;border-bottom:1px solid #d4d6d8}
.card p.hl{color:var(--blue)}
.card .meta{display:flex;justify-content:space-between;align-items:center;margin-top:20px;font-size:13px;color:var(--muted)}
.card .meta span:last-child{font-size:16px;color:var(--blue)}
.card .meta span.dark{color:var(--ink)}

/* contact */
.contact-title{left:0;top:2890px;width:1200px;text-align:center;color:var(--blue);font-size:46px;font-weight:400}
.contact-sub{left:330px;top:2962px;width:540px;text-align:center;font-size:14px;line-height:22px}
.info-row{left:160px;display:flex;gap:22px;align-items:flex-start}
.info-row svg{stroke:var(--blue);fill:none;stroke-width:2;flex:none}
.info-name{color:var(--blue);font-size:24px;font-family:"Maven Pro",sans-serif}
.info-text{font-size:17px;color:var(--ink)}
.field{left:548px;width:499px;border:1px solid var(--line);font-size:13px;color:#b9bec3;padding:12px 16px}
.submit{left:548px;top:3228px;width:186px;height:50px;background:var(--blue-deep);color:#fff;font-size:20px;display:flex;align-items:center;justify-content:center;font-family:"Maven Pro",sans-serif}

/* footer */
.footer-curve{left:0;top:3380px}
.footer-brand{left:0;top:3364px;width:1200px;text-align:center;color:var(--blue);font-size:22px;letter-spacing:1px;font-weight:600}
.footer-menu{left:0;top:3444px;width:1200px;display:flex;justify-content:center;gap:70px;font-size:13px;color:var(--muted)}
.footer-menu .active{color:var(--blue)}
.copyright{left:0;top:3488px;width:1200px;text-align:center;font-size:14px;color:var(--muted)}
.copyright b{color:var(--blue);font-weight:500}
</style>
</head>
<body>

<!-- top bar -->
<div class="abs topbar">
  <div class="item" style="left:78px">
    <svg width="16" height="22" viewBox="0 0 16 22"><path d="M8 0a8 8 0 0 0-8 8c0 6 8 14 8 14s8-8 8-14a8 8 0 0 0-8-8zm0 11a3 3 0 1 1 0-6 3 3 0 0 1 0 6z"/></svg>
    123 Building Name, Street, City, Country - Zipcode
  </div>
  <div class="item" style="left:776px">
    <svg width="16" height="16" viewBox="0 0 24 24"><path d="M6.6 10.8a15 15 0 0 0 6.6 6.6l2.2-2.2c.3-.3.7-.4 1-.2 1.1.4 2.3.6 3.6.6.6 0 1 .4 1 1V20c0 .6-.4 1-1 1A17 17 0 0 1 3 4c0-.6.4-1 1-1h3.5c.6 0 1 .4 1 1 0 1.3.2 2.5.6 3.6.1.3 0 .7-.2 1z"/></svg>
    123 456 7878
  </div>
  <div class="abs" style="left:912px;top:16px;width:1px;height:20px;background:#555"></div>
  <div class="item" style="left:934px;font-size:12px">
    <svg width="16" height="12" viewBox="0 0 16 12"><path d="M0 0h16v12H0z M1 1l7 5 7-5" fill="#fff" stroke="#121619" stroke-width="1"/></svg>
    info@brightlinelabs.com
  </div>
</div>

<!-- navigation -->
<div class="abs nav">
  <div class="brand"><span class="dot"></span>BRIGHTLINE LABS</div>
  <div class="menu">
    <span class="active">HOME</span><span>ABOUT US</span><span>SERVICES</span><span>BLOG</span><span>CONTACT US</span>
  </div>
</div>

<!-- hero -->
<div class="abs hero" role="img" aria-label="Dark blue background of glowing hexadecimal data code">
  <h1>BRIGHTLINE LABS</h1>
  <p>Lorem Ipsum is simply dummy text of the printing and typesetting industry. Lorem Ipsum has been the industry's standard dummy text ever since the 1500s, when an unknown printer took a galley of type.</p>
  <div class="btn">LEARN MORE</div>
</div>

<!-- services decorations -->
<div class="abs deco" style="left:-260px;top:880px;width:740px;height:700px;background:var(--pale)"></div>
<div class="abs deco" style="left:860px;top:1230px;width:700px;height:680px;background:var(--pale)"></div>
<div class="abs deco" style="left:996px;top:990px;width:40px;height:40px;background:#fbe7cf"></div>
<div class="abs deco" style="left:730px;top:1080px;width:50px;height:50px;background:#d8ecfa"></div>
<div class="abs deco" style="left:376px;top:1718px;width:40px;height:40px;background:#d6dcf8"></div>
<div class="abs deco" style="left:78px;top:1820px;width:50px;height:50px;background:#f9d9e2"></div>
<div class="abs deco" style="left:204px;top:1892px;width:50px;height:50px;background:#fbe7cf"></div>

<h2 class="abs services-title">OUR SERVICES</h2>
<p class="abs services-sub">Lorem Ipsum is simply dummy text of the printing and typesetting industry. Lorem Ipsum has been the industry's standard dummy text ever since the 1500s.</p>

<div class="abs spine"></div>

<!-- 1 -->
<div class="abs node" style="left:548px;top:936px">
  <svg width="46" height="40" viewBox="0 0 46 40"><rect x="2" y="2" width="42" height="28" rx="2"/><path d="M16 38h14M23 30v8M10 22l8-8 6 6 10-10"/></svg>
</div>
<div class="abs badge on" style="left:553px;top:932px">1</div>
<div class="abs service left" style="left:118px;top:982px">
  <h3>Machine learning</h3>
  <p>Lorem Ipsum is simply dummy text of the printing and typesetting industry. Lorem Ipsum has been the industry's standard dummy text ever since the 1500s.</p>
  <a>LEARN MORE</a>
</div>

<!-- 2 -->
<div class="abs node" style="left:548px;top:1196px">
  <svg width="44" height="40" viewBox="0 0 44 40"><circle cx="22" cy="8" r="5"/><circle cx="7" cy="30" r="5"/><circle cx="37" cy="30" r="5"/><path d="M19 12l-9 14M25 12l9 14M12 30h20"/></svg>
</div>
<div class="abs badge off" style="left:553px;top:1192px">2</div>
<div class="abs service right" style="left:706px;top:1242px">
  <h3>Big Data</h3>
  <p>Lorem Ipsum is simply dummy text of the printing and typesetting industry. Lorem Ipsum has been the industry's standard dummy text ever since the 1500s.</p>
  <a>LEARN MORE</a>
</div>

<!-- 3 -->
<div class="abs node" style="left:548px;top:1460px">
  <svg width="42" height="42" viewBox="0 0 42 42"><rect x="9" y="9" width="24" height="24" rx="2"/><circle cx="21" cy="21" r="5"/><path d="M15 2v7M21 2v7M27 2v7M15 33v7M21 33v7M27 33v7M2 15h7M2 21h7M2 27h7M33 15h7M33 21h7M33 27h7"/></svg>
</div>
<div class="abs badge on" style="left:553px;top:1456px">3</div>
<div class="abs service left" style="left:118px;top:1504px">
  <h3>Data Science</h3>
  <p>Lorem Ipsum is simply dummy text of the printing and typesetting industry. Lorem Ipsum has been the industry's standard dummy text ever since the 1500s.</p>
  <a>LEARN MORE</a>
</div>

<!-- 4 -->
<div class="abs node" style="left:548px;top:1720px">
  <svg width="46" height="40" viewBox="0 0 46 40"><path d="M2 38h42M8 38V26M16 38V20M24 38V24M32 38V14M40 38V18M6 18l10-8 8 6 14-12"/></svg>
</div>
<div class="abs badge off" style="left:553px;top:1716px">4</div>
<div class="abs service right" style="left:706px;top:1762px">
  <h3>Data Analytics</h3>
  <p>Lorem Ipsum is simply dummy text of the printing and typesetting industry. Lorem Ipsum has been the industry's standard dummy text ever since the 1500s.</p>
  <a>LEARN MORE</a>
</div>

<!-- about -->
<div class="abs band"></div>
<div class="abs about" role="img" aria-label="Dim photo of server racks in a data centre">
  <h2>ABOUT US</h2>
  <p style="top:124px">Lorem Ipsum is simply dummy text of the printing and typesetting industry. Lorem Ipsum has been the industry's standard dummy text ever since the 1500s, when an unknown printer took a galley of type and scrambled it to make a type specimen book. It has survived not only five centuries, but also the leap into electronic typesetting, remaining essentially unchanged.</p>
  <p style="top:210px">Lorem Ipsum is simply dummy text of the printing and typesetting industry. Lorem Ipsum has been the industry's standard dummy text ever since the 1500s, when an unknown printer took a galley of type.</p>
  <div class="btn">LEARN MORE</div>
</div>

<!-- blogs -->
<h2 class="abs blogs-title">BLOGS</h2>
<div class="abs card" style="left:78px">
  <div class="photo" role="img" aria-label="City road at night with light trails" style="background:linear-gradient(160deg,#2d3a4a,#7a6a4a 55%,#c7a25a)"></div>
  <p class="hl">Lorem Ipsum is simply dummy text of the printing and typesetting industry.</p>
  <div class="meta"><span>20, Nov 2018</span><span class="dark">Read More »</span></div>
</div>
<div class="abs card" style="left:445px">
  <div class="photo" role="img" aria-label="Desk with laptop, calculator and paperwork" style="background:linear-gradient(160deg,#5a7a8c,#9fb6c2 50%,#d7dfe3)"></div>
  <p>Lorem Ipsum is simply dummy text of the printing and typesetting industry.</p>
  <div class="meta"><span>10, Nov 2018</span><span>Read More »</span></div>
</div>
<div class="abs card" style="left:812px">
  <div class="photo" role="img" aria-label="Office worker at a desk in a bright open office" style="background:linear-gradient(160deg,#b8a58c,#8a7b69 50%,#cfc6bb)"></div>
  <p>Lorem Ipsum is simply dummy text of the printing and typesetting industry.</p>
  <div class="meta"><span>10, Nov 2018</span><span>Read More »</span></div>
</div>

<!-- contact -->
<h2 class="abs contact-title">CONTACT US</h2>
<p class="abs contact-sub">Got a question? Our 24/7 support team will go the extra mile so you can have easy and enjoyable experience with us.</p>

<div class="abs info-row" style="top:3040px">
  <svg width="24" height="30" viewBox="0 0 24 30"><path d="M12 2a9 9 0 0 0-9 9c0 7 9 17 9 17s9-10 9-17a9 9 0 0 0-9-9z" fill="var(--blue)" stroke="none"/><circle cx="12" cy="11" r="3.5" fill="#fff" stroke="none"/></svg>
  <div>
    <div class="info-name">BRIGHTLINE LABS</div>
    <div style="font-size:13px;line-height:22px;margin-top:6px;color:var(--muted)">123 Building Name, Street, City,<br>Country - Zipcode</div>
  </div>
</div>
<div class="abs info-row" style="top:3141px">
  <svg width="24" height="24" viewBox="0 0 24 24"><path d="M6.6 10.8a15 15 0 0 0 6.6 6.6l2.2-2.2c.3-.3.7-.4 1-.2 1.1.4 2.3.6 3.6.6.6 0 1 .4 1 1V20c0 .6-.4 1-1 1A17 17 0 0 1 3 4c0-.6.4-1 1-1h3.5c.6 0 1 .4 1 1 0 1.3.2 2.5.6 3.6.1.3 0 .7-.2 1z"/></svg>
  <div class="info-text">123 456 7878</div>
</div>
<div class="abs info-row" style="top:3194px">
  <svg width="24" height="20" viewBox="0 0 24 20"><rect x="2" y="2" width="20" height="16"/><path d="M2 2l10 8 10-8"/></svg>
  <div class="info-text">info@brightlinelabs.com</div>
</div>

<div class="abs field" style="top:3033px;height:45px">Name</div>
<div class="abs field" style="top:3087px;height:45px">E-Mail</div>
<div class="abs field" style="top:3141px;height:78px">Message</div>
<div class="abs submit">SUBMIT</div>

<!-- footer -->
<svg class="abs footer-curve" width="1200" height="149" viewBox="0 0 1200 149"><path d="M0 40 Q600 -30 1200 40 V149 H0z" fill="var(--pale)"/></svg>
<div class="abs footer-brand brand" style="position:absolute;justify-content:center;display:block">BRIGHTLINE LABS</div>
<div class="abs footer-menu"><span class="active">HOME</span><span>ABOUT US</span><span>SERVICES</span><span>BLOGS</span><span>CONTACT</span></div>
<div class="abs copyright">© <b>BRIGHTLINE LABS - 2018.</b> All Rights Reserved.</div>

</body>
</html>
```